Solar Company Bussiness Card

I need a 2 sided business card and would like a .psd and any font files for each side of the card. I would like my logo used, it should be attached with the fonts. I'm not opposed to the font colors with the logo being changed.

On the sample design, I'd like the following:

Marcus Dellow
President
Phone: 555-382-9174
www.brightvanepower.example

As I've recently opened in a 2nd market, I'm not sure about an address as I currently have 2 of them. I may actually get separate cards printed, one batch for each address, that's why I need the PSD file.
Updates

I'm very pleased with the response and designs I've received here for my business card. First and foremost, I'd like to thank everyone who took the time to submit a design. There truly are a lot of great designs in the bunch here and I'm having a little difficulty deciding. I will be reaching out to someone in the next day or two here to go to a final design. At this time, I'm not looking for any new concepts. If any of you do logos, I'm looking for a new logo for our sister entity, Dellow Partners, Inc. Thanks, Marcus Dellow

Reason: I'm not looking for any new designs at this point, but extending this deadline in order to give people I've asked a chance to re-submit items.

Industry/Entity Type

Business

```html
<!DOCTYPE html>
<html lang="en">
<head>
<meta charset="utf-8">
<title>Brightvane Power – Business Card</title>
<link rel="stylesheet" href="https://fonts.googleapis.com/css2?family=Open+Sans:wght@400;600;700&display=swap">
<style>
  :root{
    --brand-blue:#0a5aa6;
    --brand-blue-deep:#07498a;
    --paper:#ffffff;
    --paper-shade:#d9dadc;
    --stage:#eceef1;
    --ink-light:#ffffff;
  }
  *{margin:0;padding:0;box-sizing:border-box}
  html,body{width:1200px;height:891px;overflow:hidden;background:var(--stage);font-family:"Open Sans",sans-serif}
  .stage{position:relative;width:1200px;height:891px}
  .card{position:absolute;left:250px;width:700px;height:400px;overflow:hidden;box-shadow:0 6px 18px rgba(0,0,0,.18)}
  .card--front{top:30px;background:linear-gradient(90deg,var(--paper) 0%,var(--paper) 45%,var(--paper-shade) 100%)}
  .card--back{top:461px;background:var(--brand-blue)}

  /* front */
  .accent-bar{position:absolute;background:var(--brand-blue)}
  .accent-bar--top{left:0;top:28px;width:330px;height:14px}
  .accent-bar--top-thin{left:335px;top:28px;width:60px;height:14px}
  .contact-panel{position:absolute;left:400px;top:0;width:300px;height:290px;background:var(--brand-blue);padding:52px 0 0 40px}
  .name-panel{position:absolute;left:0;top:290px;width:340px;height:110px;background:var(--brand-blue);padding:28px 0 0 40px;color:var(--ink-light)}
  .divider{position:absolute;background:var(--brand-blue)}
  .divider--a{left:350px;top:270px;width:10px;height:60px}
  .divider--b{left:372px;top:300px;width:10px;height:60px}

  .brand{position:absolute;left:40px;top:130px;display:flex;align-items:center;gap:14px;white-space:nowrap}
  .brand-mark{width:38px;height:38px;background:var(--brand-blue);flex:none}
  .brand-name{font-weight:600;font-size:29px;color:var(--brand-blue);letter-spacing:.2px}

  .person-name{font-weight:700;font-size:22px;letter-spacing:1px;text-transform:uppercase}
  .person-title{font-size:14px;margin-top:2px}

  .contact-list{list-style:none;color:var(--ink-light);font-size:13px}
  .contact-list li{display:flex;align-items:center;gap:10px;height:28px;white-space:nowrap}
  .contact-list svg{width:13px;height:13px;fill:var(--ink-light);flex:none}

  /* back */
  .back-stripe{position:absolute;background:var(--ink-light)}
  .back-stripe--left{left:60px;top:0;width:10px;height:400px}
  .back-stripe--left-2{left:84px;top:0;width:5px;height:400px}
  .back-stripe--right{right:60px;top:0;width:10px;height:400px}
  .back-stripe--right-2{right:84px;top:0;width:5px;height:400px}
</style>
</head>
<body>
<main class="stage">
  <section class="card card--front" aria-label="Business card, front">
    <div class="accent-bar accent-bar--top"></div>
    <div class="accent-bar accent-bar--top-thin"></div>

    <div class="brand">
      <span class="brand-mark" aria-hidden="true"></span>
      <span class="brand-name">Brightvane Power</span>
    </div>

    <div class="divider divider--a"></div>
    <div class="divider divider--b"></div>

    <div class="contact-panel">
      <ul class="contact-list">
        <li><svg viewBox="0 0 16 16"><rect x="4" y="1" width="8" height="14" rx="1.5" fill="none" stroke="#fff" stroke-width="1.6"/></svg>555-382-9174</li>
        <li><svg viewBox="0 0 16 16"><path d="M3 1l3 0 1 4-2 1c1 2 3 4 5 5l1-2 4 1 0 3c0 1-1 2-2 2C7 15 1 9 1 3c0-1 1-2 2-2z"/></svg>555-382-9174</li>
        <li><svg viewBox="0 0 16 16"><path d="M1 3h14v10H1z M1 3l7 6 7-6" fill="none" stroke="#fff" stroke-width="1.5"/></svg>info@brightvanepower.example</li>
        <li><svg viewBox="0 0 16 16"><circle cx="8" cy="8" r="6.5" fill="none" stroke="#fff" stroke-width="1.4"/><path d="M1.5 8h13M8 1.5c-3 3-3 10 0 13M8 1.5c3 3 3 10 0 13" fill="none" stroke="#fff" stroke-width="1.2"/></svg>www.brightvanepower.example</li>
        <li><svg viewBox="0 0 16 16"><path d="M8 1a5 5 0 0 1 5 5c0 4-5 9-5 9S3 10 3 6a5 5 0 0 1 5-5z"/><circle cx="8" cy="6" r="1.8" fill="#0a5aa6"/></svg>12 Harbor Street, Suite 4, Lakeside</li>
      </ul>
    </div>

    <div class="name-panel">
      <p class="person-name">Marcus Dellow</p>
      <p class="person-title">President</p>
    </div>
  </section>

  <section class="card card--back" aria-label="Business card, back">
    <div class="back-stripe back-stripe--left"></div>
    <div class="back-stripe back-stripe--left-2"></div>
    <div class="back-stripe back-stripe--right"></div>
    <div class="back-stripe back-stripe--right-2"></div>
  </section>
</main>
</body>
</html>
```